Engineering Land Development Company Needs Flyer Brochure for Prospective Professional Clients

Our company provides land development site design for commercial projects. We have many repeat clients that are familiar with our work. We do not advertise our services other than a website. Most of our referrals are from existing clients. When a new client contacts us and asks for a proposal for a project we would like to have a brochure that shows our strengths, experience, and professionalism. We are selling professional services similar to a lawyer or accountant. We want new clients to feel comfortable hiring a new firm. The brochure would be one page single-side included when we submit proposals for new projects. Check out our website at tovimark.com for more info. We would like a brochure that mixes grading/excavation construction work on a job site with business professional. We will need to update the brochure so we want it in .doc .psd or some other edit format. The brochure we are using is attached. It is very two-dimensional. We need some depth.

Target Market(s)

Land developers, architects, real estate, professionals, attorneys

Industry/Entity Type

Real Estate Development

Font styles to use
Sans Serif
Other font styles liked:
• calibri

Colors
0355a3
9bcb3c

Requirements
Must have
• company logo, ability to update text and images
Nice to have
• background image(s) with text overlay
Should not have
• cartoons, harsh colors, stock photos of people, lots of boxes

```html
<!DOCTYPE html>
<html lang="en">
<head>
<meta charset="utf-8">
<title>Tovimark Engineering – Land Development Services</title>
<link rel="stylesheet" href="https://fonts.googleapis.com/css2?family=Arimo:wght@400;700&family=Lato:wght@400&family=Titillium+Web:wght@700&display=swap">
<style>
  :root {
    --brand-blue: #3a46a2;
    --brand-green: #3aae4a;
    --hero-tone-a: #4f82cc;
    --hero-tone-b: #6f98d2;
    --ink: #1d1d1d;
    --paper: #ffffff;
  }
  * { margin: 0; padding: 0; box-sizing: border-box; }
  html, body { width: 900px; height: 1200px; overflow: hidden; background: var(--paper); }
  body { font-family: "Arimo", Arial, sans-serif; color: var(--ink); position: relative; }

  .hero-photo {
    position: absolute; left: 0; top: 0; width: 900px; height: 488px;
    background: linear-gradient(180deg, var(--hero-tone-a) 0%, var(--hero-tone-b) 100%);
  }
  .rule-green { position: absolute; left: 0; width: 900px; height: 7px; background: var(--brand-green); }
  .rule-top { top: 488px; }

  .brand-bar {
    position: absolute; top: 495px; left: 0; width: 900px; height: 68px;
    display: flex; align-items: center; justify-content: center; padding-left: 110px; gap: 10px;
  }
  .brand-square { width: 30px; height: 30px; background: var(--brand-blue); }
  .brand-name { font-family: "Lato", sans-serif; font-size: 31px; color: var(--brand-blue); letter-spacing: -0.3px; }

  .mission-band {
    position: absolute; top: 565px; left: 0; width: 900px; height: 142px;
    background: var(--brand-blue); border-bottom: 6px solid var(--brand-green);
    padding: 15px 18px 0 312px; color: #fff;
  }
  .mission-title {
    font-family: "Titillium Web", sans-serif; font-size: 17.5px; line-height: 1.2; text-transform: uppercase; letter-spacing: 0.3px;
  }
  .mission-text { font-size: 13.2px; line-height: 1.25; margin-top: 7px; }

  .mission-photo {
    position: absolute; left: 78px; top: 530px; width: 206px; height: 206px; border-radius: 50%;
    border: 7px solid var(--brand-green); box-shadow: 0 0 0 5px #fff;
    background: radial-gradient(circle at 50% 40%, #b9c7d8 0%, #7f93aa 100%);
  }

  .services {
    position: absolute; top: 738px; left: 38px; width: 840px;
    display: grid; grid-template-columns: 220px 211px 212px 197px;
  }
  .service { width: 192px; }
  .service-icon { display: block; margin: 0 0 8px 48px; }
  .service-title {
    font-family: "Titillium Web", sans-serif; font-size: 13px; line-height: 1.15;
    color: var(--brand-blue); text-transform: uppercase; min-height: 70px;
  }
  .service-text { font-size: 13px; line-height: 1.18; }

  .clients {
    position: absolute; top: 1075px; left: 80px; width: 740px; border-top: 1px solid var(--brand-green);
    padding-top: 6px; text-align: center; font-size: 12.4px;
  }
  .client-list {
    position: absolute; top: 1116px; left: 42px; width: 816px;
    display: flex; justify-content: space-between; align-items: center;
    font-weight: 700; font-size: 8.6px; color: var(--brand-blue);
  }

  .rule-bottom { top: 1141px; height: 7px; }
  .contact-bar {
    position: absolute; top: 1148px; left: 0; width: 900px; height: 52px; background: var(--brand-blue);
    display: flex; align-items: center; padding-left: 46px; gap: 8px; color: #fff;
    font-weight: 700; font-size: 17px;
  }
  .contact-item { display: flex; align-items: center; gap: 7px; margin-right: 10px; }
</style>
</head>
<body>
  <div class="hero-photo" role="img" aria-label="Photo of an excavator lifting a full bucket of red clay on a grading site"></div>
  <div class="rule-green rule-top"></div>

  <header class="brand-bar">
    <span class="brand-square"></span>
    <span class="brand-name">Tovimark Engineering PLLC</span>
  </header>

  <section class="mission-band">
    <h1 class="mission-title">Our mission at Tovimark Engineering is to provide superior<br>quality professional land development services</h1>
    <p class="mission-text">Our firm provides planning, surveying, engineering, and environmental services which allows us to focus on the entire land development process rather than one specific discipline. Providing a broad scope of professional services helps to streamline a project by eliminating many disadvantages of having multiple firms with overlapping responsibilities.</p>
  </section>
  <div class="mission-photo" role="img" aria-label="Photo of a steel-framed commercial building under construction"></div>

  <section class="services">
    <article class="service">
      <svg class="service-icon" width="50" height="50" viewBox="0 0 50 50" aria-hidden="true">
        <circle cx="25" cy="25" r="22" fill="none" stroke="var(--brand-blue)" stroke-width="3"/>
        <rect x="14" y="30" width="4" height="7" fill="var(--brand-green)"/><rect x="20" y="27" width="4" height="10" fill="var(--brand-green)"/>
        <rect x="26" y="24" width="4" height="13" fill="var(--brand-green)"/><rect x="32" y="21" width="4" height="16" fill="var(--brand-green)"/>
        <path d="M13 26 L24 18 L28 21 L36 13" fill="none" stroke="var(--brand-green)" stroke-width="2.5"/>
        <path d="M31 13 L37 12 L36 18 Z" fill="var(--brand-green)"/>
      </svg>
      <h2 class="service-title">We are land development professionals who can see the “big picture”.</h2>
      <p class="service-text">We have extensive experience with site selection, due diligence investigations, re-zonings, and land planning. Every project is different. We look forward to identifying all feasible alternatives. We become part of the project and enjoy developing the best plan for the success of each particular project. We understand that time is money and unexpected delays are unacceptable.</p>
    </article>
    <article class="service">
      <svg class="service-icon" width="50" height="50" viewBox="0 0 50 50" aria-hidden="true">
        <circle cx="25" cy="25" r="22" fill="none" stroke="var(--brand-blue)" stroke-width="3"/>
        <rect x="16" y="13" width="18" height="24" rx="2" fill="none" stroke="var(--brand-green)" stroke-width="2.5"/>
        <rect x="21" y="11" width="8" height="4" fill="var(--brand-green)"/>
        <path d="M20 21h10M20 26h10M20 31h6" stroke="var(--brand-green)" stroke-width="2"/>
      </svg>
      <h2 class="service-title">We are land development professionals who provide superior quality surveying services.</h2>
      <p class="service-text">We have extensive experience with site selection, due diligence investigations, re-zonings, and land planning. Every project is different. We look forward to identifying all feasible alternatives. We become part of the project and enjoy developing the best plan for the success of each particular project. We understand that time is money and unexpected delays are unacceptable.</p>
    </article>
    <article class="service">
      <svg class="service-icon" width="50" height="50" viewBox="0 0 50 50" aria-hidden="true">
        <circle cx="25" cy="25" r="22" fill="none" stroke="var(--brand-blue)" stroke-width="3"/>
        <path d="M16 12 L16 36 L36 36 Z" fill="none" stroke="var(--brand-green)" stroke-width="2.5"/>
        <path d="M20 22 L20 32 L29 32 Z" fill="none" stroke="var(--brand-green)" stroke-width="2"/>
      </svg>
      <h2 class="service-title">We are land development professionals who can handle the most complicated engineering challenge.</h2>
      <p class="service-text">Let us worry about all the technical stuff and the regulators. Our firm has extensive experience with infrastructure assessments, erosion control, grading, roadway design, stormwater management, water systems, sewer systems, utilities, flood plain management, landscape design, permitting, bidding, and construction administration.</p>
    </article>
    <article class="service">
      <svg class="service-icon" width="50" height="50" viewBox="0 0 50 50" aria-hidden="true">
        <circle cx="25" cy="25" r="22" fill="none" stroke="var(--brand-blue)" stroke-width="3"/>
        <circle cx="25" cy="25" r="14" fill="none" stroke="var(--brand-green)" stroke-width="2.5"/>
        <path d="M17 33 C17 22 24 17 33 17 C33 26 28 33 17 33 Z" fill="var(--brand-green)"/>
      </svg>
      <h2 class="service-title">We are land development professionals who provide superior quality environmental services.</h2>
      <p class="service-text">We provide environmental site assessments, underground storage tank management, soil and groundwater sampling and testing, contamination remediation, Brownfields assessments, permitting and redevelopment, and wetlands permitting. Our firm works closely with state and federal agencies to provide economical mitigation and remediation solutions.</p>
    </article>
  </section>

  <p class="clients">Our business would not be successful without the support of our clients. Some of our project clients include</p>
  <div class="client-list">
    <span>Parkland</span><span>Crustle</span><span>Glazeway</span><span>Stackhouse</span><span>Verdo</span>
    <span>Pie Barn</span><span>Gearline</span><span>Fieldmore</span><span>Buildwell</span><span>Kaizu</span>
    <span>Linkstar</span><span>Harvo</span><span>Salsera</span><span>Tacoria</span><span>Grocemart</span>
    <span>Brewlane</span><span>Wingfield</span><span>Burgette</span><span>Pawhaus</span>
  </div>

  <div class="rule-green rule-bottom"></div>
  <footer class="contact-bar">
    <span class="contact-item">
      <svg width="12" height="17" viewBox="0 0 12 17" aria-hidden="true"><path d="M6 0C2.7 0 0 2.6 0 5.9 0 10 6 17 6 17s6-7 6-11.1C12 2.6 9.3 0 6 0z" fill="var(--brand-green)"/><circle cx="6" cy="6" r="2.2" fill="var(--brand-blue)"/></svg>
      418 Oak Avenue – Suite 120 Millbrook, NC 28601
    </span>
    <span class="contact-item">
      <svg width="18" height="14" viewBox="0 0 18 14" aria-hidden="true"><path d="M1 4C1 1 4 0 9 0s8 1 8 4v2h-4V4H5v2H1z" fill="var(--brand-green)"/><rect x="4" y="7" width="10" height="7" rx="1" fill="var(--brand-green)"/></svg>
      (555) 014-2760
    </span>
    <span class="contact-item">
      <svg width="15" height="15" viewBox="0 0 16 16" aria-hidden="true"><circle cx="8" cy="8" r="7.5" fill="var(--brand-green)"/><path d="M1 8h14M8 1c-3 3-3 11 0 14M8 1c3 3 3 11 0 14" stroke="var(--brand-blue)" stroke-width="1" fill="none"/></svg>
      www.tovimark.com
    </span>
  </footer>
</body>
</html>
```